Brightway Haus Inc. Business Card Design

Brightway Haus Inc. is in search of a great clean design for our business cards!

Looking to incorporate our full logo and watermark on side one (however, I am open to having the text and watermark separated within the design.)

On side two, I am looking to have contact information (Name, Position, Phone #, Email, Website (www.thebrightwayhaus.ca). Can have the logo and/or watermark as part of the design if applicable.

Please add tagline "Where Shine Counts" on either side 1 or 2. This tagline can be in a sans serif, serif or cursive font as long as it compliments overall design. Capitalization can be title or sentence case depending on how it fits within the design.

Get creative!! Looking for a clean, crisp, premium design! Looking for a glossy card finish with spot UV features when printed. Cards will also be printed with rounded corners. Standard dimensions (3.5 x 2).

Target Market(s)

B2B - primary clients are business owners or property management corporations. (residential jobs are few and far between)

Industry/Entity Type

Business

Contact Information for Business Card

- clean, crisp design
- double sided
- spot UV accents and glossy finish upon printing
- standard business card size (3.5 x 2) with rounded corners
- please see project description for requirements per side

Font styles to use
Sans Serif

Requirements
Must have
• - adequate bleeds with print ready files
• - cohesive design elements between side 1 & 2
• - spot UV elements (can be on both sides or just one, use your discretion)
• - colour pallet should match the logo file provided
• - incorporate tagline "where shine counts" (this tagline can be in a serif or sans serif font as long as it is complimentary to the overall design.
Nice to have
• - Premium elements with a clean design
Should not have
• - Please omit cartoon or whimsical like designs, think premium.
• - Colours should not stray from the pallet of the provided logo.

```html
<!DOCTYPE html>
<html lang="en">
<head>
<meta charset="UTF-8">
<title>Brightway Haus Inc. Business Card</title>
<link href="https://fonts.googleapis.com/css2?family=Open+Sans:ital,wght@0,400;0,700;0,800;1,400&family=Roboto+Condensed:wght@400;500&family=Roboto:wght@400&display=swap" rel="stylesheet">
<style>
  :root {
    --backdrop: #2b2b2d;
    --teal: #12b2b3;
    --navy: #1b2553;
    --paper: #f2f2f2;
    --white: #ffffff;
    --grey: #a9a9a9;
  }
  * { margin: 0; padding: 0; box-sizing: border-box; }
  html, body {
    width: 1200px; height: 960px; overflow: hidden;
    background: var(--backdrop);
  }
  .canvas { position: relative; width: 1200px; height: 960px; }

  .card {
    position: absolute;
    width: 600px; height: 343px;
    border-radius: 22px;
    overflow: hidden;
  }

  /* Contact side */
  .card-contact { left: 314px; top: 113px; background: var(--teal); color: var(--white); }
  .watermark-area {
    position: absolute; left: 222px; top: 0; width: 378px; height: 343px;
    background:
      radial-gradient(ellipse 55% 60% at 62% 62%, rgba(242,242,242,0.85) 0%, rgba(242,242,242,0.45) 45%, rgba(242,242,242,0) 75%),
      linear-gradient(160deg, rgba(27,37,83,0) 55%, rgba(27,37,83,0.55) 100%);
  }
  .person { position: absolute; left: 37px; top: 40px; font-family: "Roboto Condensed", sans-serif; }
  .person-name { font-size: 21px; font-weight: 500; letter-spacing: 0.2px; line-height: 24px; }
  .person-role { font-size: 16px; font-weight: 500; line-height: 20px; margin-top: 2px; letter-spacing: 0.2px; }

  .address {
    position: absolute; left: 37px; top: 162px;
    font-family: "Roboto", sans-serif; font-size: 14.5px; line-height: 18px;
  }
  .contact-list {
    position: absolute; left: 37px; top: 207px; list-style: none;
    font-family: "Roboto", sans-serif; font-size: 14.5px; line-height: 19.2px;
  }
  .contact-list li { display: flex; align-items: center; gap: 7px; }
  .contact-list svg { width: 13px; height: 13px; fill: var(--white); flex: none; }

  /* Brand side */
  .card-brand { left: 311px; top: 472px; background: var(--paper); }
  .brand {
    position: absolute; left: 0; right: 0; top: 150px;
    display: flex; justify-content: center; align-items: center; gap: 10px;
  }
  .brand-square { width: 30px; height: 30px; background: var(--teal); }
  .brand-name {
    font-family: "Open Sans", sans-serif; font-weight: 800;
    font-size: 31px; letter-spacing: -0.5px; color: var(--navy);
  }
  .tagline {
    position: absolute; left: 0; right: 0; top: 276px;
    display: flex; justify-content: center; align-items: center; gap: 6px;
    font-family: "Open Sans", sans-serif; font-style: italic; font-size: 18px; color: var(--navy);
  }
  .tagline-accent { color: var(--teal); }
  .tagline-rule { width: 112px; height: 1px; }
  .tagline-rule.left { background: linear-gradient(to right, transparent, var(--navy)); }
  .tagline-rule.right { background: linear-gradient(to left, transparent, var(--navy)); }
</style>
</head>
<body>
<div class="canvas">

  <section class="card card-contact">
    <div class="watermark-area" role="img" aria-label="Large brand watermark symbol"></div>
    <div class="person">
      <div class="person-name">DANIEL HARLOW</div>
      <div class="person-role">CEO/FOUNDER</div>
    </div>
    <div class="address">
      <div>2140 Willowmere Road</div>
      <div>Kelowna, BC V1Y 4K2</div>
    </div>
    <ul class="contact-list">
      <li><svg viewBox="0 0 16 16" aria-hidden="true"><path d="M3.6 1l2.6 3-1.4 1.8a9 9 0 0 0 5.4 5.4L12 9.8l3 2.6-1.6 2.4C7.6 14.6 1.4 8.4 1.2 2.6z"/></svg>250 555 0148</li>
      <li><svg viewBox="0 0 16 16" aria-hidden="true"><path d="M4.5 0h7a1.5 1.5 0 0 1 1.5 1.5v13a1.5 1.5 0 0 1-1.5 1.5h-7A1.5 1.5 0 0 1 3 14.5v-13A1.5 1.5 0 0 1 4.5 0zm.5 2v10h6V2zm3 11a1 1 0 1 0 0 2 1 1 0 0 0 0-2z"/></svg>250 555 0172</li>
      <li><svg viewBox="0 0 16 16" aria-hidden="true"><path d="M4 1h8v4H4zM1 6h14v7h-3v2H4v-2H1zm4 5v3h6v-3z"/></svg>250 555 0199</li>
      <li><svg viewBox="0 0 16 16" aria-hidden="true"><path d="M1 3h14v1.2L8 9 1 4.2zm0 2.6l7 4.8 7-4.8V13H1z"/></svg>info@thebrightwayhaus.ca</li>
      <li><svg viewBox="0 0 16 16" aria-hidden="true"><path d="M8 1a7 7 0 1 0 0 14A7 7 0 0 0 8 1zm-1 2.5L9.5 5 8 7.5 5 8 4 6zm3.5 5l2 1.5-2.5 3.5-2-1z"/></svg>www.thebrightwayhaus.ca</li>
    </ul>
  </section>

  <section class="card card-brand">
    <div class="brand">
      <span class="brand-square"></span>
      <span class="brand-name">BRIGHTWAY HAUS INC.</span>
    </div>
    <div class="tagline">
      <span class="tagline-rule left"></span>
      <span>Where <span class="tagline-accent">Shine</span> Counts</span>
      <span class="tagline-rule right"></span>
    </div>
  </section>

</div>
</body>
</html>
```